Fitness Equipment Repair Business Needs a Catchy New Business Card

We have an existing business card, however, it is quite plain and boring. We are expanding primarily in the commercial area (gyms, studios, apartment complexes etc). The business card will serve as eye candy to those managers/owners that can't be met for a face to face.
Originally I was planning for a brochure as well, but all of our information is better summarized on our website. (brightloopservice.ca).
I would like the card to match the colour scheme of the website and utilize the logo. It should have a professional clean feel to it, however, a little colouring outside the lines wouldn't hurt.
The example card is for my service technician (Colin Marsh). If possible I would like to be able to edit the text to use for more than one person.

Industry/Entity Type

Appliance Repair

Contact Information for Business Card

Clean, crisp and professional but needs to be eye catching. Preferably using the black, white and red colour scheme matching the website. Double sided would be nice, but is not necessary.

Colors
ec1f27
ffffff
000000

Requirements
Must have
• Must be able to edit name, phone number and title to use for multiple people. Must show the company website (brightloopservice.ca).

```html
<!DOCTYPE html>
<html lang="en">
<head>
<meta charset="utf-8">
<title>Brightloop Service – Business Card</title>
<link rel="stylesheet" href="https://fonts.googleapis.com/css2?family=Cinzel:wght@600&family=Open+Sans:wght@400&family=PT+Sans:ital@1&display=swap">
<style>
  :root {
    --red: #ec1f27;
    --white: #ffffff;
    --black: #000000;
    --soft-white: #e6e6e6;
    --divider: #5a5a5a;
    --backdrop: #e9e6e2;
  }
  * { margin: 0; padding: 0; box-sizing: border-box; }
  html, body {
    width: 1200px; height: 987px; overflow: hidden;
    background: var(--backdrop);
  }
  .canvas { position: relative; width: 1200px; height: 987px; }
  .card {
    position: absolute; left: 293px; width: 615px; height: 350px;
    box-shadow: 0 2px 6px rgba(0,0,0,.25);
  }
  .card--front { top: 130px; background: var(--black); }
  .card--back { top: 506px; background: var(--red); }

  .brand {
    position: absolute; display: flex; align-items: center; gap: 10px;
    font-family: "Cinzel", serif; font-weight: 600; color: var(--white);
    letter-spacing: .06em; white-space: nowrap;
  }
  .brand__dot { width: 12px; height: 12px; border-radius: 50%; background: var(--red); flex: none; }
  .card--front .brand { left: 62px; top: 164px; font-size: 15px; }
  .card--back .brand { right: 34px; top: 250px; font-size: 17px; }
  .card--back .brand__dot { background: var(--white); }

  .divider {
    position: absolute; left: 343px; top: 63px; width: 1px; height: 211px;
    background: linear-gradient(to bottom, transparent, var(--divider) 20%, var(--divider) 80%, transparent);
  }
  .details {
    position: absolute; left: 371px; top: 70px;
    font-family: "Open Sans", sans-serif; color: var(--soft-white);
  }
  .details__name {
    font-family: "Cinzel", serif; font-weight: 600; font-size: 22px;
    color: var(--red); letter-spacing: .03em; line-height: 1;
  }
  .details__title {
    font-family: "Cinzel", serif; font-weight: 600; font-size: 16px;
    color: var(--soft-white); letter-spacing: .05em; margin-top: 6px; line-height: 1;
  }
  .details__address { font-size: 15.5px; line-height: 23px; margin-top: 16px; }
  .details__contacts { list-style: none; margin-top: 10px; font-size: 15.5px; line-height: 23.5px; }
  .details__contacts li { display: flex; align-items: center; gap: 9px; }
  .icon { width: 14px; height: 14px; fill: var(--red); flex: none; }

  .card--back .website {
    position: absolute; right: 30px; top: 302px;
    font-family: "PT Sans", sans-serif; font-style: italic; font-size: 17px; color: var(--white);
  }
</style>
</head>
<body>
<main class="canvas">
  <section class="card card--front" aria-label="Card front">
    <div class="brand"><span class="brand__dot"></span>Brightloop Service</div>
    <div class="divider"></div>
    <div class="details">
      <h1 class="details__name">Colin Marsh</h1>
      <p class="details__title">Service technician</p>
      <p class="details__address">1875 Carrow Lane NW<br>Edmonton AB T5K 2P4</p>
      <ul class="details__contacts">
        <li><svg class="icon" viewBox="0 0 24 24"><path d="M6.6 10.8a15.1 15.1 0 0 0 6.6 6.6l2.2-2.2a1 1 0 0 1 1-.25 11.4 11.4 0 0 0 3.6.57 1 1 0 0 1 1 1V20a1 1 0 0 1-1 1A17 17 0 0 1 3 4a1 1 0 0 1 1-1h3.5a1 1 0 0 1 1 1c0 1.25.2 2.45.57 3.57a1 1 0 0 1-.25 1z"/></svg>587-555-0148</li>
        <li><svg class="icon" viewBox="0 0 24 24"><path d="M6.6 10.8a15.1 15.1 0 0 0 6.6 6.6l2.2-2.2a1 1 0 0 1 1-.25 11.4 11.4 0 0 0 3.6.57 1 1 0 0 1 1 1V20a1 1 0 0 1-1 1A17 17 0 0 1 3 4a1 1 0 0 1 1-1h3.5a1 1 0 0 1 1 1c0 1.25.2 2.45.57 3.57a1 1 0 0 1-.25 1z"/></svg>780-555-0193</li>
        <li><svg class="icon" viewBox="0 0 24 24"><path d="M2 5h20v14H2z M3 6l9 7 9-7" fill="var(--red)" stroke="var(--black)" stroke-width="1.4"/></svg>hello@brightloopservice.ca</li>
        <li><svg class="icon" viewBox="0 0 24 24"><circle cx="12" cy="12" r="10"/><path d="M2 12h20M12 2c3 3 3 17 0 20M12 2c-3 3-3 17 0 20" fill="none" stroke="var(--black)" stroke-width="1.4"/></svg>brightloopservice.ca</li>
      </ul>
    </div>
  </section>

  <section class="card card--back" aria-label="Card back">
    <div class="brand"><span class="brand__dot"></span>Brightloop Service</div>
    <p class="website">brightloopservice.ca</p>
  </section>
</main>
</body>
</html>
```